Nanny Share Ecommerce Website for Finding Childcare and Parents who need Childcare BrightPramHub.net

Our company needs an ecommerce website (BrightPramHub.net) for a US subscription based service strictly for nanny sharing that connects families and caregivers. The website would allow families to connect with one another as well as to search for nannies. The service would be searchable for other families by location (by radius or zip code), children demographic (age range/gender/special needs), days of week or times, after school care, school closure days (holidays), etc. The service would also be searchable for nannies based on gender, provider age range, years experience, language, hourly rate, transportation available, certification (CPR first aid), education etc. The search fields would be searchable and sortable and allow to connect with the provider (after paying subscription fee). The service would be similar to tendlyfolk.net in that it would allow for families and caregivers to post photos as well as a short bio of the themselves. There would also be a feedback/star rating mechanism to rate caregivers who have performed work for families (viewable to public). The service would be free for nannies to post their bios and only a subscription based service for families to connect with other families or with caregivers (able to view bio but need service to connect). There will be a short bio on the benefits of nanny sharing (reduced cost, increased flexibility for parents, reduced illness, increased socialization with other children vs. sole nanny), as well as Q&A section with best practices.

Target Market(s)

Families, Nannies

Industry/Entity Type

Childcare

Logo Text

Bright Pram Hub

Coding

Coded - Design and coding required

Number of Pages Required

5+ page

Requirements
Must have
• Searchable (need to be able to search for families as well as nannies), responsive, functional, easy to use, add value to families and nannies. Needs to be able to collect payment for subscription.
Nice to have
• Optimized for mobile, SEO optimized

```html
<!DOCTYPE html>
<html lang="en">
<head>
<meta charset="utf-8">
<title>Bright Pram Hub – Connects families and Caregivers</title>
<link href="https://fonts.googleapis.com/css2?family=Fredoka:wght@500;600&family=Open+Sans:ital,wght@0,400;0,600;0,700;1,400&display=swap" rel="stylesheet">
<style>
:root{
  --cyan:#1ec0e8;
  --pink:#f06a9a;
  --ink:#2b2b2b;
  --text:#666;
  --muted:#8a8a8a;
  --line:#e3e3e3;
  --faq-bg:#f4f4f4;
  --footer:#232323;
  --white:#fff;
}
*{box-sizing:border-box;margin:0;padding:0}
html,body{width:1200px;height:4000px;overflow:hidden}
body{font-family:"Open Sans",Arial,sans-serif;color:var(--text);background:var(--white);position:relative}
.section{position:absolute;left:0;width:1200px;overflow:hidden}
.abs{position:absolute}
.heading{font-family:"Fredoka","Open Sans",sans-serif;font-weight:600;color:var(--ink);font-size:40px;text-align:center;position:absolute;left:0;width:1200px}
.heading span{position:relative;display:inline-block;padding:0 30px}
.heading span::before,.heading span::after{content:"";position:absolute;top:50%;width:90px;height:1px;background:#d5d5d5}
.heading span::before{right:100%}
.heading span::after{left:100%}
.heading.light{color:var(--white)}
.heading.light span::before,.heading.light span::after{background:rgba(255,255,255,.6)}

/* header */
.site-header{top:0;height:107px;border-top:4px solid var(--cyan);background:var(--white)}
.brand{left:99px;top:28px;display:flex;align-items:center;gap:12px}
.brand-dot{width:44px;height:44px;border-radius:50%;background:var(--cyan)}
.brand-name{font-family:"Open Sans",sans-serif;font-weight:700;font-size:27px;color:var(--ink)}
.main-nav{top:43px;left:0;width:1200px;font-size:15px;color:#444}
.main-nav a{position:absolute;color:inherit;text-decoration:none}
.main-nav a.active{color:var(--cyan)}
.search-icon{left:1086px;top:44px}

/* hero */
.hero{top:107px;height:546px}
.hero-photo{position:absolute;inset:0;background:linear-gradient(100deg,#cfc6bd 0%,#b89a86 35%,#a77d68 55%,#d9cfc4 80%,#ece7e1 100%)}
.hero-shade{position:absolute;inset:0;background:linear-gradient(180deg,rgba(0,0,0,0) 40%,rgba(0,0,0,.25) 100%)}
.hero-title{top:285px;left:0;width:1200px;text-align:center;font-family:"Fredoka",sans-serif;font-weight:600;font-size:50px;color:var(--white)}
.btn{position:absolute;height:40px;border-radius:20px;font-size:14px;font-weight:700;text-transform:uppercase;display:flex;align-items:center;justify-content:center;letter-spacing:.3px}
.btn-cyan{background:var(--cyan);color:var(--white)}
.btn-ghost{border:2px solid var(--white);color:var(--white)}
.slider-arrow{width:40px;height:40px;border-radius:50%;background:rgba(255,255,255,.25);top:252px;display:flex;align-items:center;justify-content:center}

/* services */
.services{top:653px;height:480px}
.service-photo{width:210px;height:210px;border-radius:50%;border:6px solid var(--white);box-shadow:0 0 0 1px #ddd,0 4px 14px rgba(0,0,0,.12);top:180px}
.service-text{top:178px;width:230px;font-size:14px;line-height:23px}
.service-text h3{font-size:19px;font-weight:600;color:var(--ink);margin-bottom:10px;line-height:26px}
.service-text.left{left:125px;text-align:right}
.service-text.right{left:848px}
.btn-outline-pink{position:absolute;top:329px;width:112px;height:36px;border:2px solid #f7a9c3;color:var(--pink);border-radius:18px;font-size:12px;font-weight:600;display:flex;align-items:center;justify-content:center}

/* benefits */
.benefits{top:1133px;height:440px;background:linear-gradient(100deg,#e677ad 0%,#b68bd0 40%,#6fb2e6 70%,#2fc3ea 100%)}
.benefit{top:160px;width:250px;text-align:center;color:var(--white)}
.benefit svg{display:block;margin:0 auto 14px}
.benefit h3{font-size:18px;font-weight:600;line-height:22px;margin-bottom:6px}
.benefit p{font-size:13px;line-height:19px;opacity:.92;padding:0 18px}
.benefit .chev{margin:10px auto 0}

/* about */
.about{top:1573px;height:608px}
.eyebrow{left:99px;top:140px;font-size:17px;color:var(--cyan)}
.about h2{left:99px;top:175px;width:560px;font-size:36px;line-height:44px;color:var(--ink);font-weight:700}
.about p{left:99px;top:290px;width:590px;font-size:14px;line-height:24px}
.btn-learn{left:99px;top:400px;width:142px;height:42px;background:var(--cyan);color:var(--white);border-radius:21px;font-size:14px;font-weight:600;display:flex;align-items:center;justify-content:center}
.about-photo{left:699px;top:80px;width:501px;height:528px;background:radial-gradient(circle at 45% 35%,#f2e0cf 0%,#ead2bd 35%,#f6efe7 60%,transparent 75%),radial-gradient(circle at 70% 95%,#c6d24a 0%,#b7c43d 25%,transparent 45%),#fff}

/* faq */
.faq{top:2181px;height:587px;background:var(--faq-bg)}
.faq-item{left:165px;width:870px;height:43px;background:var(--white);border:1px solid var(--line);display:flex;align-items:center;padding:0 18px;font-size:14px;color:#555}
.faq-item .q{color:var(--pink);font-weight:700;margin-right:8px}
.faq-item .toggle{margin-left:auto;color:#999;font-size:16px}
.faq-item.open{background:var(--pink);border-color:var(--pink);color:var(--white)}
.faq-item.open .q,.faq-item.open .toggle{color:var(--white)}
.faq-answer{left:165px;top:208px;width:870px;height:65px;background:var(--white);border:1px solid var(--line);border-top:0;padding:12px 24px;font-size:12.5px;line-height:20px;color:var(--muted)}

/* how it works */
.how{top:2768px;height:552px;background:linear-gradient(100deg,#f36b98 0%,#e07ab5 35%,#7fb0e4 70%,#2cc1ea 100%)}
.tab{position:absolute;top:213px;height:42px;border-radius:21px;font-size:17px;display:flex;align-items:center;justify-content:center}
.tab-active{left:368px;width:224px;background:#f35e93;color:var(--white)}
.tab-active::after{content:"";position:absolute;left:50%;bottom:-8px;margin-left:-8px;border:8px solid transparent;border-bottom:0;border-top-color:#f35e93}
.tab-idle{left:605px;width:230px;border:2px solid var(--white);color:var(--white)}
.step{top:283px;width:240px;text-align:center;color:var(--white);font-size:17px;font-weight:600;line-height:23px}
.step .ring{width:104px;height:104px;border-radius:50%;background:var(--white);border:4px solid rgba(255,255,255,.55);background-clip:padding-box;margin:0 auto 18px;display:flex;align-items:center;justify-content:center;box-shadow:0 0 0 4px rgba(255,255,255,.35)}
.step-link{top:332px;width:130px;border-top:2px dashed rgba(255,255,255,.8)}

/* testimonials */
.testimonials{top:3320px;height:427px}
.avatar{width:96px;height:96px;border-radius:50%;border:3px solid var(--cyan);padding:4px;top:187px}
.avatar div{width:100%;height:100%;border-radius:50%;background:linear-gradient(160deg,#d9d3cc,#8f8a86)}
.avatar.pink{border-color:var(--pink)}
.quote{top:180px;width:350px;font-size:13px;line-height:21px;font-style:italic;color:var(--muted)}
.sign{top:280px;width:350px;text-align:right;font-size:16px;color:var(--ink);font-weight:600}
.stars{top:303px;width:350px;text-align:right;font-size:15px;letter-spacing:1px;color:var(--cyan)}
.stars.pink{color:var(--pink)}

/* footer */
.site-footer{top:3747px;height:253px;background:var(--footer);border-top:4px solid var(--cyan)}
.social{top:64px;width:36px;height:36px;border-radius:50%;border:2px solid #ddd}
.footer-nav{top:131px;left:0;width:1200px;text-align:center;font-size:14px;color:#e5e5e5}
.footer-nav b{font-weight:400;margin:0 14px;color:#bbb}
.copyright{top:170px;left:0;width:1200px;text-align:center;font-size:12px;color:#ccc}
</style>
</head>
<body>

<header class="section site-header">
  <div class="abs brand"><div class="brand-dot"></div><div class="brand-name">Bright Pram Hub</div></div>
  <nav class="abs main-nav">
    <a class="active" style="left:480px">Home</a>
    <a style="left:570px">About us</a>
    <a style="left:676px">Services</a>
    <a style="left:778px">Feedbacks</a>
    <a style="left:894px">FAQ</a>
    <a style="left:970px">Contact us</a>
  </nav>
  <svg class="abs search-icon" width="16" height="16" viewBox="0 0 16 16" fill="none" stroke="#f06a9a" stroke-width="2"><circle cx="6.5" cy="6.5" r="4.5"/><path d="M10 10l4 4"/></svg>
</header>

<section class="section hero">
  <div class="hero-photo" role="img" aria-label="Photo of a mother and young daughter playing with colourful building blocks"></div>
  <div class="hero-shade"></div>
  <div class="abs slider-arrow" style="left:20px"><svg width="12" height="14" viewBox="0 0 12 14"><path d="M8 2L3 7l5 5" fill="none" stroke="#fff" stroke-width="2"/></svg></div>
  <div class="abs slider-arrow" style="left:1140px"><svg width="12" height="14" viewBox="0 0 12 14"><path d="M4 2l5 5-5 5" fill="none" stroke="#fff" stroke-width="2"/></svg></div>
  <h1 class="abs hero-title">Connects families and Caregivers</h1>
  <div class="btn btn-cyan" style="left:413px;top:369px;width:147px">Find Families</div>
  <div class="btn btn-ghost" style="left:592px;top:369px;width:197px">Search for Nannies</div>
</section>

<section class="section services">
  <h2 class="heading" style="top:80px"><span>Our Services</span></h2>
  <div class="abs service-text left">
    <h3>Matching families</h3>
    <p>Find nearby families with kids of similar ages to share one nanny.</p>
  </div>
  <div class="btn-outline-pink" style="left:243px">READ MORE</div>
  <div class="abs service-photo" style="left:370px" role="img" aria-label="Photo of a smiling family of four"></div>
  <div class="abs service-photo" style="left:620px" role="img" aria-label="Photo of a family with grandparents and children"></div>
  <div class="abs service-photo" style="left:370px;background:linear-gradient(150deg,#e9d7c7,#b98d72 60%,#7a5a4a)"></div>
  <div class="abs service-photo" style="left:620px;background:linear-gradient(150deg,#efe6dc,#c9a990 55%,#8f6f5d)"></div>
  <div class="abs service-text right">
    <h3>Helping connect families to nannies</h3>
    <p>Browse vetted caregivers, read reviews and connect in a few clicks.</p>
  </div>
  <div class="btn-outline-pink" style="left:848px">READ MORE</div>
</section>

<section class="section benefits" role="img" aria-label="Soft photo of hands and a child behind a pink to blue gradient">
  <h2 class="heading light" style="top:80px"><span>Our benefits</span></h2>
  <div class="abs benefit" style="left:94px">
    <svg width="46" height="52" viewBox="0 0 46 52" fill="none" stroke="#fff" stroke-width="2"><circle cx="23" cy="28" r="20"/><path d="M29 20c-2-3-12-3-12 2s12 3 12 9-10 5-12 2M23 14v28"/></svg>
    <h3>Reduced cost</h3>
    <p>Split one nanny's rate between two families and save on care.</p>
    <svg class="chev" width="14" height="10" viewBox="0 0 14 10" fill="none" stroke="#fff" stroke-width="2"><path d="M2 1l5 4 5-4M2 5l5 4 5-4"/></svg>
  </div>
  <div class="abs benefit" style="left:342px">
    <svg width="56" height="52" viewBox="0 0 56 52" fill="none" stroke="#fff" stroke-width="2"><circle cx="16" cy="9" r="6"/><circle cx="40" cy="9" r="6"/><path d="M8 50V22h16v28M32 50V22h16v28M16 50V34M40 50V34"/></svg>
    <h3>Increased flexibility<br>for parents</h3>
    <p>Shared schedules give parents more options for days and hours.</p>
    <svg class="chev" width="14" height="10" viewBox="0 0 14 10" fill="none" stroke="#fff" stroke-width="2"><path d="M2 1l5 4 5-4M2 5l5 4 5-4"/></svg>
  </div>
  <div class="abs benefit" style="left:582px">
    <svg width="52" height="52" viewBox="0 0 52 52" fill="none" stroke="#fff" stroke-width="2"><circle cx="20" cy="10" r="6"/><path d="M12 50V24h16v26M28 30l10-10 8 8M38 20v-8h8"/></svg>
    <h3>Reduced illness</h3>
    <p>Fewer children in care means fewer colds going around.</p>
    <svg class="chev" width="14" height="10" viewBox="0 0 14 10" fill="none" stroke="#fff" stroke-width="2"><path d="M2 1l5 4 5-4M2 5l5 4 5-4"/></svg>
  </div>
  <div class="abs benefit" style="left:867px">
    <svg width="60" height="52" viewBox="0 0 60 52" fill="none" stroke="#fff" stroke-width="2"><circle cx="14" cy="12" r="6"/><circle cx="44" cy="20" r="5"/><path d="M6 50V26h16v24M38 50V32h12v18M26 30h8M30 26v8"/></svg>
    <h3>Increased socialization<br>with other children<br>vs. sole nanny</h3>
    <p>Kids learn to share and play with a steady friend.</p>
    <svg class="chev" width="14" height="10" viewBox="0 0 14 10" fill="none" stroke="#fff" stroke-width="2"><path d="M2 1l5 4 5-4M2 5l5 4 5-4"/></svg>
  </div>
</section>

<section class="section about">
  <div class="abs eyebrow">Bright Pram Hub</div>
  <h2 class="abs">We Are More Than Just a Nanny Agency</h2>
  <p class="abs">Bright Pram Hub helps families share trusted caregivers close to home. Search by zip code, ages, schedule and special needs, then meet families and nannies who fit your routine. Every profile has a bio, photos and star ratings from real families.</p>
  <div class="abs btn-learn">Learn More</div>
  <div class="abs about-photo" role="img" aria-label="Photo of a smiling woman holding a baby on a green exercise ball"></div>
</section>

<section class="section faq">
  <h2 class="heading" style="top:88px"><span>Frequently asked Questions</span></h2>
  <div class="abs faq-item open" style="top:168px"><span class="q">Q .</span>How do placeat facere possimus, omnis voluptas assumen?<span class="toggle">&#8853;</span></div>
  <p class="abs faq-answer">Most shares pair two families with one nanny, alternating homes each week and splitting the hourly rate evenly.</p>
  <div class="abs faq-item" style="top:294px"><span class="q">Q .</span>If arum facilis est et expedita distin?<span class="toggle">&#8853;</span></div>
  <div class="abs faq-item" style="top:347px"><span class="q">Q .</span>If ero eos et accusamus et iusto odio?<span class="toggle">&#8853;</span></div>
  <div class="abs faq-item" style="top:400px"><span class="q">Q .</span>Where again is there anyone who loves?<span class="toggle">&#8853;</span></div>
  <div class="abs faq-item" style="top:453px"><span class="q">Q .</span>Why facilis est et expedita distin?<span class="toggle">&#8853;</span></div>
</section>

<section class="section how" role="img" aria-label="Soft photo of a child's room behind a pink to blue gradient">
  <h2 class="heading light" style="top:92px"><span>How it Works</span></h2>
  <div class="tab tab-active">Search Nannies</div>
  <div class="tab tab-idle">Search Families</div>
  <div class="abs step" style="left:107px">
    <div class="ring"><svg width="40" height="40" viewBox="0 0 40 40" fill="#1ec0e8"><circle cx="20" cy="13" r="8"/><path d="M5 37c0-9 7-14 15-14s15 5 15 14z"/></svg></div>
    Review Profiles
  </div>
  <div class="abs step-link" style="left:180px"></div>
  <div class="abs step" style="left:360px">
    <div class="ring"><svg width="40" height="40" viewBox="0 0 40 40" fill="none" stroke="#1ec0e8" stroke-width="3"><rect x="5" y="8" width="26" height="26" rx="3"/><path d="M17 25l3-8 14-12 4 4-14 12z"/></svg></div>
    Sign-up to Connect to<br>Families &amp; Nannies
  </div>
  <div class="abs step-link" style="left:545px"></div>
  <div class="abs step" style="left:608px">
    <div class="ring"><svg width="38" height="38" viewBox="0 0 24 24" fill="#1ec0e8"><path d="M6.6 10.8a15 15 0 006.6 6.6l2.2-2.2c.3-.3.7-.4 1-.2 1.1.4 2.3.6 3.6.6.6 0 1 .4 1 1V20c0 .6-.4 1-1 1A17 17 0 013 4c0-.6.4-1 1-1h3.5c.6 0 1 .4 1 1 0 1.3.2 2.5.6 3.6.1.3 0 .7-.2 1z"/></svg></div>
    Contact Families<br>and Caregivers
  </div>
  <div class="abs step-link" style="left:796px"></div>
  <div class="abs step" style="left:859px">
    <div class="ring"><svg width="40" height="40" viewBox="0 0 40 40" fill="none" stroke="#1ec0e8" stroke-width="3"><circle cx="20" cy="15" r="8"/><path d="M10 8h20M6 37c0-9 6-13 14-13s14 4 14 13z"/></svg></div>
    Hire a Nanny
  </div>
</section>

<section class="section testimonials">
  <h2 class="heading" style="top:92px"><span>What Clients Say</span></h2>
  <div class="abs avatar" style="left:107px" role="img" aria-label="Portrait of a client"><div></div></div>
  <p class="abs quote" style="left:227px">We found a family two blocks away and a wonderful nanny within a week. Sharing care cut our costs in half.</p>
  <div class="abs sign" style="left:227px">~ Marisol</div>
  <div class="abs stars" style="left:227px">&#9733;&#9733;&#9733;&#9733;&#9733;</div>
  <div class="abs avatar pink" style="left:635px" role="img" aria-label="Portrait of a client"><div></div></div>
  <p class="abs quote" style="left:755px">The search filters made it easy to find a caregiver with CPR training who speaks Spanish. Highly recommended.</p>
  <div class="abs sign" style="left:755px">~ Marisol</div>
  <div class="abs stars pink" style="left:755px">&#9733;&#9733;&#9733;&#9733;&#9733;</div>
</section>

<footer class="section site-footer">
  <div class="abs social" style="left:467px"></div>
  <div class="abs social" style="left:511px"></div>
  <div class="abs social" style="left:555px"></div>
  <div class="abs social" style="left:599px"></div>
  <div class="abs social" style="left:643px"></div>
  <div class="abs social" style="left:687px"></div>
  <nav class="abs footer-nav">Home<b>/</b>About us<b>/</b>Services<b>/</b>How it works<b>/</b>FAQ<b>/</b>Contact us</nav>
  <div class="abs copyright">© Copyright 2018 Bright Pram Hub. All Rights Reserved</div>
</footer>

</body>
</html>
```